Request for Business Card Design

Hi. My name is Marlene, I am looking for a new business card design for my company, Quarrow Signal Instruments, LLC. I really like the design you did for Tarsel Venture and was hoping you could do something similar using our full logo and our mark. I am also open to any raised texture design using our mark. I have attached our full logo, which would need to be somewhere on the card, as well as the mark in both outline and full form, as well as our brand colors / guide. The card does not have to be white, as long as our logo and mark appear. I actually like darker colored business cards more, but am open to all options. If you are interested in working with me, please let me know. We would also take the business card design into letterhead design if you can do that.

```html
<!DOCTYPE html>
<html lang="en">
<head>
<meta charset="utf-8">
<title>Quarrow Signal Instruments – Business Card</title>
<link rel="stylesheet" href="https://fonts.googleapis.com/css2?family=Open+Sans:wght@400;600;700;800&display=swap">
<style>
  :root {
    --backdrop: #232324;
    --card: #3b3b3d;
    --card-deep: #333335;
    --card-deeper: #2c2c2e;
    --brand-blue: #1e9dd3;
    --text-light: #ffffff;
    --mark-tone: #2b2b2d;
  }
  * { box-sizing: border-box; margin: 0; padding: 0; }
  html, body {
    width: 1200px; height: 780px; overflow: hidden;
    background: var(--backdrop);
    font-family: "Open Sans", Arial, sans-serif;
  }
  .stage {
    position: relative; width: 1200px; height: 780px;
    display: flex; justify-content: center; align-items: center; gap: 70px;
  }
  .card {
    position: relative; width: 340px; height: 594px;
    background: var(--card); border-radius: 26px; overflow: hidden;
  }

  /* Back side */
  .card-back .mark-block {
    position: absolute; left: 50%; top: 50%;
    transform: translate(-50%, -50%) rotate(-90deg);
    display: flex; align-items: center; gap: 22px;
    white-space: nowrap;
  }
  .card-back .mark-dot {
    width: 86px; height: 86px; border-radius: 50%;
    background: var(--mark-tone);
  }
  .card-back .mark-name {
    font-weight: 800; font-size: 34px; letter-spacing: 3px;
    color: var(--mark-tone); text-transform: uppercase;
    line-height: 1.05;
  }

  /* Front side */
  .card-front .decor { position: absolute; inset: 0; }
  .brand-row {
    position: absolute; top: 48px; left: 0; right: 0;
    display: flex; justify-content: center; align-items: center; gap: 10px;
  }
  .brand-dot { width: 30px; height: 30px; border-radius: 50%; background: var(--brand-blue); }
  .brand-name {
    font-weight: 700; font-size: 14px; letter-spacing: 1.2px;
    color: var(--text-light); text-transform: uppercase;
  }
  .person {
    position: absolute; top: 196px; left: 0; right: 0; text-align: center;
  }
  .person-name { font-weight: 800; font-size: 40px; color: var(--brand-blue); line-height: 1; }
  .person-role { font-weight: 600; font-size: 15px; color: var(--text-light); margin-top: 4px; }
  .contact-list {
    position: absolute; top: 300px; left: 0; right: 0;
    list-style: none; text-align: center;
    font-size: 14.5px; line-height: 22px; color: var(--text-light);
  }
  .address {
    position: absolute; top: 498px; left: 0; right: 0; text-align: center;
    font-size: 15px; line-height: 21px; color: var(--text-light);
  }
</style>
</head>
<body>
<main class="stage">

  <section class="card card-back" aria-label="Card back">
    <div class="mark-block">
      <div class="mark-dot"></div>
      <div class="mark-name">Quarrow Signal<br>Instruments</div>
    </div>
  </section>

  <section class="card card-front" aria-label="Card front">
    <svg class="decor" width="340" height="594" viewBox="0 0 340 594">
      <!-- lower layered bands -->
      <path d="M0 420 Q170 470 340 330 L340 594 L0 594 Z" fill="var(--card-deep)"/>
      <path d="M0 400 Q200 450 340 320 L340 380 Q230 470 60 440 L0 432 Z" fill="var(--card-deeper)"/>
      <path d="M0 590 Q120 520 230 440 L340 420 L340 594 Z" fill="var(--card)" opacity="0.55"/>

      <!-- contact bracket frames -->
      <g fill="none" stroke="var(--brand-blue)" stroke-width="2">
        <polyline points="114,276 24,304 24,370 54,370"/>
        <polyline points="226,276 316,276 316,342 292,342"/>
        <polyline points="140,283 60,300 60,318 80,318"/>
        <polyline points="200,283 276,283 276,300 260,300"/>
      </g>
      <g fill="var(--brand-blue)">
        <polygon points="54,365 62,370 54,375"/>
        <polygon points="292,337 284,342 292,347"/>
        <polygon points="80,313 88,318 80,323"/>
        <polygon points="260,295 252,300 260,305"/>
      </g>

      <!-- contact icons -->
      <g>
        <circle cx="128" cy="278" r="11" fill="var(--brand-blue)"/>
        <rect x="122" y="274" width="12" height="8" fill="none" stroke="#fff" stroke-width="1.4"/>
        <polyline points="122,274 128,279 134,274" fill="none" stroke="#fff" stroke-width="1.4"/>

        <circle cx="156" cy="278" r="11" fill="var(--brand-blue)"/>
        <path d="M151 273 q1 -1 3 0 l1 3 -2 1 q1 3 4 4 l1 -2 3 1 q1 2 0 3 q-6 1 -10 -10z" fill="#fff"/>

        <circle cx="184" cy="278" r="11" fill="var(--brand-blue)"/>
        <rect x="178" y="274" width="12" height="9" rx="1" fill="#fff"/>
        <rect x="180" y="271" width="8" height="4" fill="#fff"/>

        <circle cx="212" cy="278" r="11" fill="var(--brand-blue)"/>
        <circle cx="212" cy="278" r="6" fill="none" stroke="#fff" stroke-width="1.4"/>
        <line x1="206" y1="278" x2="218" y2="278" stroke="#fff" stroke-width="1.2"/>
        <ellipse cx="212" cy="278" rx="2.5" ry="6" fill="none" stroke="#fff" stroke-width="1.2"/>
      </g>

      <!-- location pin -->
      <circle cx="170" cy="476" r="12" fill="var(--brand-blue)"/>
      <path d="M170 484 l-4.5 -7 a5 5 0 1 1 9 0 z" fill="#fff"/>
      <circle cx="170" cy="474" r="1.8" fill="var(--brand-blue)"/>
    </svg>

    <div class="brand-row">
      <div class="brand-dot"></div>
      <div class="brand-name">Quarrow Signal Instruments</div>
    </div>

    <div class="person">
      <div class="person-name">Marlene</div>
      <div class="person-role">Director</div>
    </div>

    <ul class="contact-list">
      <li>+001 555 210 4830</li>
      <li>+001 555 210 4871</li>
      <li>info@quarrowsignal.com</li>
      <li>www.quarrowsignal.com</li>
    </ul>

    <address class="address" style="font-style: normal;">
      1180 Harbor Line Road •<br>Fairview, CO 80999
    </address>
  </section>

</main>
</body>
</html>
```